Apparel store needs a cover for their seasonal catalogue

Every season the store creates a catalogue with a preview of the collection for the customers, the catalogue is printed and sent to 25 000 customers.We need a cover and back cover project for the upcoming winter season.Here is the current summer catalogue - https://www.le-sabot-vert.com/catalogue.shtmlFormat165mmx240mmAttached is some older issues, please note that the name LE SABOT MIRANVEL should be written on it as well as automne - hiver 2019 (fall-winter 19).

Target Market(s)

medium to high price consumers - male and female

Industry/Entity Type

Shoe Store

Colors

Designer to choose colors to be used in the design.

Requirements
Must have
• company name - LE SABOT MIRANVEL
• season - automne hiver 2019
• "Arty feel" to it
Nice to have
• Creative ideas - abstract themes
• As exemple I uploaded some older cover, but you do not have to follow the same patterns
Should not have
• product images

```html
<!DOCTYPE html>
<html lang="en">
<head>
<meta charset="utf-8">
<title>Le Sabot Miranvel – Automne Hiver 2019 catalogue cover</title>
<link href="https://fonts.googleapis.com/css2?family=Montserrat:wght@400;500;700;800;900&display=swap" rel="stylesheet">
<style>
:root{
  --stage:#e4e4e4;
  --violet-top:#8a4fa3;
  --violet-mid:#5e3a8f;
  --violet-deep:#33296f;
  --orange:#e8541e;
  --label-red:#e0203c;
  --white:#ffffff;
  --line:rgba(255,255,255,.55);
  --badge-ring:#8ab43e;
}
*{box-sizing:border-box;margin:0;padding:0}
html,body{width:1200px;height:1117px;overflow:hidden}
body{background:var(--stage);font-family:'Montserrat',sans-serif;color:var(--white);position:relative}
.sheet{position:absolute;top:151px;width:560px;height:815px;overflow:hidden;
  background:linear-gradient(170deg,var(--violet-top) 0%,var(--violet-mid) 50%,var(--violet-deep) 100%);
  box-shadow:0 10px 30px rgba(0,0,0,.18)}
.sheet--back{left:25px}
.sheet--front{left:615px}

.art-band{position:absolute;left:0;width:100%;height:110px}
.art-band--top{top:0;background:linear-gradient(100deg,transparent 0%,rgba(159,216,207,.55) 35%,rgba(238,127,176,.7) 60%,rgba(42,159,216,.6) 85%,transparent 100%);
  -webkit-mask:linear-gradient(180deg,#000 30%,transparent);mask:linear-gradient(180deg,#000 30%,transparent)}
.art-band--bottom{bottom:0;background:linear-gradient(80deg,rgba(42,159,216,.6) 0%,rgba(159,216,207,.7) 30%,rgba(238,127,176,.75) 60%,rgba(255,255,255,.4) 80%,transparent 100%);
  -webkit-mask:linear-gradient(0deg,#000 40%,transparent);mask:linear-gradient(0deg,#000 40%,transparent)}

/* Front */
.cover-badge{position:absolute;left:120px;top:170px;width:320px;height:320px;border-radius:50%;
  background:var(--white);border:14px solid var(--badge-ring)}
.brand-name{position:absolute;left:0;right:0;top:515px;text-align:center;font-weight:900;font-size:38px;letter-spacing:3px;color:var(--white)}
.season-pill{position:absolute;left:110px;top:600px;width:340px;height:54px;border-radius:27px;background:var(--orange);
  border:3px solid var(--white);display:flex;align-items:center;justify-content:center;font-weight:800;font-size:24px;letter-spacing:1px}

/* Back */
.contact-title{position:absolute;top:92px;left:0;right:0;text-align:center;font-weight:900;font-size:36px;letter-spacing:2px}
.timeline{position:absolute;left:24px;right:24px;top:160px;display:grid;grid-template-columns:1fr 34px 1fr;row-gap:14px}
.timeline::before{content:"";position:absolute;left:50%;top:10px;bottom:10px;width:1px;background:var(--line)}
.node{grid-column:2;align-self:center;justify-self:center;width:22px;height:22px;transform:rotate(45deg);
  border:1.5px solid var(--orange);background:var(--violet-mid);position:relative;z-index:1}
.node::after{content:"";position:absolute;inset:6px;border-radius:50%;background:var(--white)}
.dept-label{align-self:center;background:var(--white);color:var(--label-red);font-weight:700;font-size:14px;padding:7px 14px;justify-self:start}
.cell-left.dept-label{justify-self:end}
.info-box{border:1px solid var(--line);padding:8px 10px;font-size:9.5px;line-height:1.5;font-weight:500}
.info-box strong{font-weight:700;font-size:9.5px;white-space:nowrap}
.info-line{display:flex;gap:6px;align-items:center}
.info-line svg{flex:none;width:10px;height:10px}
.cell-left{grid-column:1}
.cell-right{grid-column:3}
.hours-pill{position:absolute;left:30px;right:30px;top:622px;height:80px;border-radius:40px;background:var(--orange);
  border:3px solid var(--white);text-align:center;display:flex;flex-direction:column;justify-content:center;align-items:center;gap:6px}
.hours-main{font-weight:800;font-size:14.5px;letter-spacing:.3px;white-space:nowrap}
.hours-sub{font-weight:700;font-size:13px;display:flex;justify-content:center;gap:26px;white-space:nowrap}
</style>
</head>
<body>

<section class="sheet sheet--back" aria-label="Back cover">
  <div class="art-band art-band--top" role="img" aria-label="Abstract painted brush strokes and confetti shapes"></div>
  <h2 class="contact-title">CONTACT WITH US</h2>

  <div class="timeline">
    <div class="cell-left"></div><span class="node"></span><span class="dept-label cell-right">Customer service</span>
    <div class="info-box cell-left">
      <div class="info-line"><svg viewBox="0 0 10 10"><circle cx="5" cy="5" r="5" fill="#fff"/></svg>12 Rue des Tanneurs, ZA Les Prés Verts, 59870 Miranvel</div>
      <div class="info-line"><svg viewBox="0 0 10 10"><circle cx="5" cy="5" r="5" fill="#fff"/></svg>03 21 48 17 60</div>
      <div class="info-line"><svg viewBox="0 0 10 10"><circle cx="5" cy="5" r="5" fill="#fff"/></svg>Monday to Friday from 9am to 5.30pm</div>
      <div class="info-line"><svg viewBox="0 0 10 10"><circle cx="5" cy="5" r="5" fill="#fff"/></svg>eshop@le-sabot-vert.com</div>
    </div>
    <span class="node"></span>
    <div class="info-box cell-right">For product proposals, send the information by email to<br><strong>service-fournisseurs@le-sabot-vert.com</strong></div>

    <span class="dept-label cell-left">Purchasing department</span><span class="node"></span><span class="dept-label cell-right">Recruitment</span>

    <div class="info-box cell-left">Send your resume and cover letter by email to<br><strong>rh@le-sabot-vert.com</strong></div>
    <span class="node"></span>
    <div class="info-box cell-right">
      <div class="info-line"><svg viewBox="0 0 10 10"><circle cx="5" cy="5" r="5" fill="#fff"/></svg>8/10 rue du Marché Neuf, 59420 Norvaux</div>
      <div class="info-line"><svg viewBox="0 0 10 10"><circle cx="5" cy="5" r="5" fill="#fff"/></svg>03 21 64 29 05</div>
    </div>

    <span class="dept-label cell-left">Norvaux Store</span><span class="node"></span><span class="dept-label cell-right">Belcourt store</span>

    <div class="info-box cell-left">
      <div class="info-line"><svg viewBox="0 0 10 10"><circle cx="5" cy="5" r="5" fill="#fff"/></svg>5 Place de la Halle, 59830 Belcourt</div>
      <div class="info-line"><svg viewBox="0 0 10 10"><circle cx="5" cy="5" r="5" fill="#fff"/></svg>03 21 52 38 14</div>
    </div>
    <span class="node"></span>
    <div class="info-box cell-right">
      <div class="info-line"><svg viewBox="0 0 10 10"><circle cx="5" cy="5" r="5" fill="#fff"/></svg>Route de Vallon, Place des Artisans, 59690 Aubrelle</div>
      <div class="info-line"><svg viewBox="0 0 10 10"><circle cx="5" cy="5" r="5" fill="#fff"/></svg>03 21 77 40 13</div>
    </div>

    <span class="dept-label cell-left">Aubrelle store</span><span class="node"></span><div class="cell-right"></div>
  </div>

  <div class="hours-pill">
    <p class="hours-main">SUMMER HOURS FROM 29/7 TO 30/8: 9AM TO 4.30PM</p>
    <p class="hours-sub"><span>Closed on August 15th</span><span>www.le-sabot-vert.com</span></p>
  </div>
  <div class="art-band art-band--bottom" role="img" aria-label="Abstract painted brush strokes in pink, aqua and blue"></div>
</section>

<section class="sheet sheet--front" aria-label="Front cover">
  <div class="art-band art-band--top" role="img" aria-label="Abstract painted brush strokes and confetti shapes"></div>
  <div class="cover-badge"></div>
  <h1 class="brand-name">LE SABOT MIRANVEL</h1>
  <p class="season-pill">AUTOMNE - HIVER 2019</p>
  <div class="art-band art-band--bottom" role="img" aria-label="Abstract painted brush strokes in pink, aqua and blue"></div>
</section>

</body>
</html>
```